Envelope Design - Winner can do follow-up business

- Varnoko.com is a Swiss-based online store selling business shirts and accessories for business men
- Please visit the webpage to make yourself familiar with the company. Although the text is in German, with Plimbo translator you should be able to understand the main content.
- Our clients are mainly business men between 30 and 60 years old. Mostly with a high income working in the service industry (banking, insurance, lawyers, etc.). Sometimes there wives purchase the shirts for them ;-)
- The colors and the logo are given, as they are also used for the print materials (please see files in attachment)
- I am running several businesses and often need a talented web designer --> the winner gets substantial follow-up business
your task:
-for our company we need a new envelope design
-It should be simple and modern
-please use one of the logos in the followings.
-suprise me :)

```html
<!DOCTYPE html>
<html lang="en">
<head>
<meta charset="utf-8">
<title>Varnoko Envelope Set</title>
<link rel="stylesheet" href="https://fonts.googleapis.com/css2?family=Montserrat:wght@500&family=Roboto+Slab:wght@400&display=swap">
<style>
  :root {
    --backdrop: #e9e6e2;
    --paper: #ffffff;
    --paper-shade: #f3f3f5;
    --flap-red: #ee2e27;
    --flap-black: #000000;
    --accent-red: #e4262b;
    --brand-gold: #e2d267;
    --ink: #2b2b2b;
  }
  html, body {
    margin: 0;
    padding: 0;
    width: 1200px;
    height: 942px;
    overflow: hidden;
    background: var(--backdrop);
  }
  .canvas {
    position: relative;
    width: 1200px;
    height: 942px;
  }
  .envelope-back {
    position: absolute;
    background: var(--paper);
    box-shadow: 0 2px 6px rgba(0,0,0,0.18);
  }
  .envelope-back svg { display: block; }
  .envelope-back--red { left: 150px; top: 39px; width: 1006px; height: 450px; }
  .envelope-back--black {
    left: 117px; top: 237px; width: 1008px; height: 450px;
    background: linear-gradient(160deg, var(--paper-shade), var(--paper));
  }
  .envelope-front {
    position: absolute;
    left: 51px; top: 455px;
    width: 1007px; height: 449px;
    background: var(--paper);
    box-shadow: 0 2px 8px rgba(0,0,0,0.22);
    overflow: hidden;
  }
  .front-band {
    position: absolute; left: 0; top: 0;
    width: 100%; height: 44px;
    background: var(--flap-black);
    border-bottom: 2px solid var(--accent-red);
  }
  .front-footer-band {
    position: absolute; left: 0; bottom: 0;
    width: 100%; height: 5px;
    background: var(--brand-gold);
  }
  .brand {
    position: absolute; left: 23px; top: 112px;
    display: flex; align-items: center; gap: 12px;
  }
  .brand-mark {
    width: 14px; height: 14px;
    background: var(--accent-red);
  }
  .brand-name {
    font-family: "Montserrat", sans-serif;
    font-weight: 500;
    font-size: 36px;
    letter-spacing: 1px;
    color: var(--brand-gold);
    line-height: 1;
  }
  .contact-line {
    position: absolute; left: 24px;
    display: flex; align-items: center; gap: 12px;
    font-family: "Roboto Slab", serif;
    font-size: 15px;
    color: var(--ink);
  }
  .contact-line svg { display: block; }
  .contact-line--address { top: 181px; }
  .contact-line--web { top: 457px; }
</style>
</head>
<body>
<main class="canvas">

  <div class="envelope-back envelope-back--red">
    <svg width="1006" height="450" viewBox="0 0 1006 450" aria-hidden="true">
      <path d="M0 0 H1006 C995 25 990 45 985 62 C978 85 960 95 920 102 L575 176 C555 180 510 182 490 176 L90 102 C50 95 30 85 22 62 C17 45 12 25 0 0 Z" fill="var(--flap-red)"/>
    </svg>
  </div>

  <div class="envelope-back envelope-back--black">
    <svg width="1008" height="450" viewBox="0 0 1008 450" aria-hidden="true">
      <path d="M0 0 H1008 C997 25 992 45 987 62 C980 85 962 95 922 102 L577 176 C557 180 512 182 492 176 L90 102 C50 95 30 85 22 62 C17 45 12 25 0 0 Z" fill="var(--flap-black)"/>
    </svg>
  </div>

  <section class="envelope-front">
    <div class="front-band"></div>

    <div class="brand">
      <span class="brand-mark"></span>
      <span class="brand-name">VARNOKO</span>
    </div>

    <div class="contact-line contact-line--address">
      <svg width="14" height="18" viewBox="0 0 14 18" aria-hidden="true">
        <path d="M7 0 C3 0 0 3 0 7 C0 12 7 18 7 18 C7 18 14 12 14 7 C14 3 11 0 7 0 Z" fill="var(--accent-red)"/>
        <circle cx="7" cy="7" r="2.6" fill="var(--paper)"/>
      </svg>
      <span>Street Name, City Name State Zipcode</span>
    </div>

    <div class="contact-line contact-line--web">
      <svg width="16" height="16" viewBox="0 0 16 16" aria-hidden="true" fill="none" stroke="var(--accent-red)" stroke-width="1.2">
        <circle cx="8" cy="8" r="7"/>
        <ellipse cx="8" cy="8" rx="3" ry="7"/>
        <line x1="1" y1="8" x2="15" y2="8"/>
        <line x1="2.2" y1="4.5" x2="13.8" y2="4.5"/>
        <line x1="2.2" y1="11.5" x2="13.8" y2="11.5"/>
      </svg>
      <span>www.varnoko.com</span>
    </div>

    <div class="front-footer-band"></div>
  </section>

</main>
</body>
</html>
```